Stylish Business Cards Wanted

- DOUBLE SIDED Design Required -

High end, edgy cards for a corporate and personal stylist. Must include logo,
Name: Belinda Harwick
Title: Director and Stylist
telephone : +61 8 7142 5809
email: belinda@theloombriefing.example
website: theloombriefing.example
Tag: Corporate Workwear & Uniform Specialist | Personal Stylist
Would like nice icons for telephone, email, website

Target Market(s)

Businesses wanting stylish uniforms, people wanting stylish wardrobes

Industry/Entity Type

Corporate Workwear Stylist

Contact Information for Business Card

I would like black, white and gold foiling incorporated in the design - possibly a touch of the other colours on my branding guide attached Name: Belinda Harwick Title: Director and Stylist telephone : +61 8 7142 5809 email: belinda@theloombriefing.example website: theloombriefing.example Tag: Corporate Workwear & Uniform Specialist | Personal Stylist Would like nice icons for telephone, email, website

Font styles to use
Other font styles liked:
• Raleway

Colors

Designer to choose colors to be used in the design.

Requirements
Must have
• Gold foil accents

```html
<!DOCTYPE html>
<html lang="en">
<head>
<meta charset="utf-8">
<title>The Loom Briefing — Business Cards</title>
<link rel="stylesheet" href="https://fonts.googleapis.com/css2?family=Montserrat:wght@400;500;700&display=swap">
<style>
  :root {
    --page: #2b2b2b;
    --card: #232323;
    --gold: #e2b84e;
    --white: #ffffff;
    --ghost: rgba(255, 255, 255, 0.05);
  }
  * { margin: 0; padding: 0; box-sizing: border-box; }
  html, body { width: 1200px; height: 900px; overflow: hidden; }
  body {
    background: var(--page);
    font-family: "Montserrat", sans-serif;
    display: flex;
    flex-direction: column;
    align-items: center;
    justify-content: center;
    gap: 36px;
  }
  .card {
    width: 700px;
    height: 400px;
    background: var(--card);
    position: relative;
    overflow: hidden;
    box-shadow: 0 10px 24px rgba(0, 0, 0, 0.45);
  }

  /* Front */
  .card-front .brand {
    position: absolute;
    left: 0; right: 0; top: 120px;
    text-align: center;
    color: var(--white);
    font-weight: 700;
    font-size: 44px;
    letter-spacing: 1px;
  }
  .card-front .tagline {
    position: absolute;
    left: 0; right: 0; top: 232px;
    text-align: center;
    color: var(--gold);
    font-weight: 500;
    font-size: 13.5px;
    letter-spacing: 1.6px;
  }

  /* Back */
  .card-back .brand-ghost {
    position: absolute;
    left: 0; right: 0; top: 120px;
    text-align: center;
    color: var(--ghost);
    font-weight: 700;
    font-size: 110px;
    letter-spacing: -2px;
    white-space: nowrap;
  }
  .card-back .contact-block {
    position: absolute;
    left: 60px; right: 40px; top: 150px;
    display: flex;
    align-items: center;
  }
  .identity {
    text-align: right;
    padding-right: 22px;
    width: 280px;
  }
  .identity .name {
    color: var(--gold);
    font-weight: 700;
    font-size: 25px;
    letter-spacing: 1.5px;
    white-space: nowrap;
  }
  .identity .role {
    color: var(--white);
    font-size: 16px;
    margin-top: 2px;
    letter-spacing: 0.5px;
  }
  .divider {
    width: 2px;
    height: 84px;
    background: var(--gold);
  }
  .details {
    list-style: none;
    padding-left: 22px;
  }
  .details li {
    display: flex;
    align-items: center;
    gap: 10px;
    color: var(--white);
    font-size: 15.5px;
    letter-spacing: 0.4px;
    line-height: 28px;
    white-space: nowrap;
  }
  .details svg { width: 16px; height: 16px; flex: none; }
</style>
</head>
<body>

  <section class="card card-front" aria-label="Card front">
    <div class="brand">The Loom Briefing</div>
    <div class="tagline">CORPORATE WORKWEAR | UNIFORM SPECIALIST | PERSONAL STYLIST</div>
  </section>

  <section class="card card-back" aria-label="Card back">
    <div class="brand-ghost" aria-hidden="true">Loom Briefing</div>
    <div class="contact-block">
      <div class="identity">
        <div class="name">BELINDA HARWICK</div>
        <div class="role">Director and Stylist</div>
      </div>
      <div class="divider"></div>
      <ul class="details">
        <li>
          <svg viewBox="0 0 24 24" aria-hidden="true"><path fill="#e2b84e" d="M6.6 10.8a15.1 15.1 0 0 0 6.6 6.6l2.2-2.2c.3-.3.7-.4 1-.2 1.1.4 2.3.6 3.6.6.6 0 1 .4 1 1V20c0 .6-.4 1-1 1A17 17 0 0 1 3 4c0-.6.4-1 1-1h3.5c.6 0 1 .4 1 1 0 1.3.2 2.5.6 3.6.1.3 0 .7-.2 1z"/></svg>
          +61 8 7142 5809
        </li>
        <li>
          <svg viewBox="0 0 24 24" aria-hidden="true"><path fill="#e2b84e" d="M2 5h20v14H2z"/><path fill="none" stroke="#232323" stroke-width="1.6" d="M2 5l10 8 10-8M2 19l7-7M22 19l-7-7"/></svg>
          belinda@theloombriefing.example
        </li>
        <li>
          <svg viewBox="0 0 24 24" aria-hidden="true"><circle cx="12" cy="12" r="10" fill="none" stroke="#e2b84e" stroke-width="2"/><path fill="none" stroke="#e2b84e" stroke-width="1.6" d="M2 12h20M12 2c3 3 3 17 0 20M12 2c-3 3-3 17 0 20"/></svg>
          www.theloombriefing.example
        </li>
      </ul>
    </div>
  </section>

</body>
</html>
```